Business Card Design

New business card design

Target Market(s)

Residential & Commercial Property Managers

Industry/Entity Type

Plumbing Services

Contact Information for Business Card

Name - Rowan Keddle, title - Director, Phone Number - 0431 286 517, email - rowan@tbk-plumbing.com.au, Company ABN - 73 215 904 386,

Font styles to use
Sans Serif

Colors
0054AA
0677BA
7BADD7
CADEEF
E8F1F8

```html
<!DOCTYPE html>
<html lang="en">
<head>
<meta charset="utf-8">
<title>TBK Plumbing Services – Business Card</title>
<link rel="stylesheet" href="https://fonts.googleapis.com/css2?family=Montserrat:wght@400;500;700&display=swap">
<style>
  :root {
    --page-bg: #e8f1f8;
    --card-bg: #ffffff;
    --ink-navy: #1c2630;
    --ink-body: #222a31;
    --brand-blue: #0677ba;
    --brand-deep: #0054aa;
    --brand-light: #7badd7;
    --brand-pale: #cadeef;
    --card-shadow: 0 10px 28px rgba(0, 84, 170, 0.14);
  }
  * { box-sizing: border-box; margin: 0; padding: 0; }
  html, body {
    width: 1200px;
    height: 900px;
    overflow: hidden;
    background: var(--page-bg);
    font-family: "Montserrat", Arial, sans-serif;
  }
  .sheet {
    width: 1200px;
    height: 900px;
    display: flex;
    flex-direction: column;
    align-items: center;
    justify-content: center;
    gap: 40px;
  }
  .card {
    position: relative;
    width: 640px;
    height: 366px;
    background: var(--card-bg);
    box-shadow: var(--card-shadow);
    overflow: hidden;
  }

  /* Brand lockup: name plus one plain circle */
  .brand {
    display: flex;
    align-items: center;
    gap: 14px;
  }
  .brand-dot {
    flex: none;
    border-radius: 50%;
    background: var(--brand-blue);
  }
  .brand-name {
    color: var(--ink-navy);
    font-weight: 500;
    letter-spacing: 0.02em;
    white-space: nowrap;
  }

  /* Front */
  .card-front {
    display: flex;
    align-items: center;
    justify-content: center;
  }
  .card-front .brand-dot { width: 30px; height: 30px; }
  .card-front .brand-name { font-size: 38px; }

  /* Back */
  .card-back .brand {
    position: absolute;
    left: 44px;
    top: 48px;
    gap: 10px;
  }
  .card-back .brand-dot { width: 20px; height: 20px; }
  .card-back .brand-name { font-size: 26px; }

  .contact-block {
    position: absolute;
    left: 0;
    top: 166px;
    padding-left: 44px;
  }
  .name-bar {
    position: absolute;
    left: 0;
    top: 4px;
    width: 26px;
    height: 62px;
    background: var(--brand-light);
  }
  .person-name {
    color: var(--brand-blue);
    font-weight: 700;
    font-size: 30px;
    line-height: 1.1;
  }
  .person-title {
    color: var(--ink-body);
    font-size: 19px;
    margin-top: 4px;
  }
  .contact-list {
    list-style: none;
    margin-top: 22px;
    font-size: 18px;
    color: var(--ink-body);
  }
  .contact-list li {
    display: flex;
    align-items: center;
    gap: 10px;
    margin-top: 6px;
  }
  .contact-icon { width: 18px; height: 18px; flex: none; }
  .company-abn {
    position: absolute;
    right: 36px;
    bottom: 44px;
    font-size: 15px;
    color: var(--ink-body);
    white-space: nowrap;
  }
</style>
</head>
<body>
  <main class="sheet">
    <section class="card card-front" aria-label="Card front">
      <div class="brand">
        <span class="brand-dot"></span>
        <p class="brand-name">TBK Plumbing Services</p>
      </div>
    </section>

    <section class="card card-back" aria-label="Card back">
      <div class="brand">
        <span class="brand-dot"></span>
        <p class="brand-name">TBK Plumbing Services</p>
      </div>

      <div class="contact-block">
        <span class="name-bar"></span>
        <h1 class="person-name">Rowan Keddle</h1>
        <p class="person-title">Director</p>
        <ul class="contact-list">
          <li>
            <svg class="contact-icon" viewBox="0 0 24 24" aria-hidden="true">
              <path fill="var(--brand-blue)" d="M6.6 10.8a15.1 15.1 0 0 0 6.6 6.6l2.2-2.2c.3-.3.7-.4 1-.2 1.1.4 2.3.6 3.6.6.6 0 1 .4 1 1V20c0 .6-.4 1-1 1A17 17 0 0 1 3 4c0-.6.4-1 1-1h3.5c.6 0 1 .4 1 1 0 1.3.2 2.5.6 3.6.1.3 0 .7-.2 1z"/>
            </svg>
            <span>0431 286 517</span>
          </li>
          <li>
            <svg class="contact-icon" viewBox="0 0 24 24" aria-hidden="true">
              <rect x="2" y="5" width="20" height="14" rx="2" fill="none" stroke="var(--brand-blue)" stroke-width="2"/>
              <path d="M3 6l9 7 9-7" fill="none" stroke="var(--brand-blue)" stroke-width="2"/>
            </svg>
            <span>rowan@tbk-plumbing.com.au</span>
          </li>
        </ul>
      </div>

      <p class="company-abn">Company ABN - 73 215 904 386</p>
    </section>
  </main>
</body>
</html>
```